New Business Cards for Tormin Group

We need a new Business Card to compliment our new logo. We are a vibrant design, manufacture and install business providing recreation areas, public parks and Municipal spaces. We want business cards that are classy, modern and clean.

We have recently changed our logo, and are celebrating our 40th anniversary. We want business cards with a new modern design to reflect our status.

Target Market(s)

Customers

Contact Information for Business Card

We need all the details of our 3 offices as per the business card attached. Please disregard the old logo on the business card, the other three files show our new logo.

Requirements
Must have
• All info as per attached business card but with new logo.
Nice to have

```html
<!DOCTYPE html>
<html lang="en">
<head>
<meta charset="utf-8">
<title>Tormin Group – Business Card</title>
<link rel="stylesheet" href="https://fonts.googleapis.com/css2?family=Lato:wght@400;700&display=swap">
<style>
  :root {
    --backdrop: #5c5c5c;
    --card: #ffffff;
    --accent-red: #e8303a;
    --ink-dark: #444446;
    --ink-soft: #6e6e70;
    --band-dark: #4a4a4c;
    --band-light: #5f5f61;
    --rule: #6a6a6a;
  }
  html, body {
    margin: 0;
    width: 1200px;
    height: 1200px;
    overflow: hidden;
    background: var(--backdrop);
    font-family: "Lato", sans-serif;
  }
  .business-card {
    position: absolute;
    left: 50px;
    top: 280px;
    width: 1100px;
    height: 640px;
    background: var(--card);
    border-radius: 43px;
    overflow: hidden;
  }
  .business-card > * { position: absolute; margin: 0; line-height: 1; white-space: nowrap; }
  .brand {
    right: 52px;
    top: 106px;
    display: flex;
    align-items: center;
    gap: 14px;
  }
  .brand-dot {
    width: 52px; height: 52px;
    border-radius: 50%;
    background: var(--accent-red);
  }
  .brand-name {
    font-weight: 700;
    font-size: 44px;
    color: var(--ink-dark);
  }
  .person-name { left: 40px; top: 144px; font-size: 41px; color: var(--accent-red); font-weight: 400; }
  .person-title { left: 40px; top: 193px; font-size: 27px; color: var(--ink-dark); }
  .direct-line { left: 40px; font-size: 20px; font-weight: 700; color: var(--ink-dark); }
  .direct-phone { top: 280px; }
  .direct-email { top: 323px; }
  .divider { left: 40px; top: 372px; width: 636px; height: 3px; background: var(--rule); }
  .office { font-size: 20px; color: var(--ink-soft); }
  .office h2 { margin: 0 0 16px; font-size: 26px; font-weight: 400; color: var(--accent-red); line-height: 1; }
  .office p { margin: 0 0 13.5px; line-height: 1; }
  .office-head { left: 40px; top: 393px; }
  .office-dubai { left: 418px; top: 393px; }
  .office-doha { left: 772px; top: 398px; }
  .footer-bands { left: 0; bottom: 0; width: 1100px; height: 69px; }
  .web-address { left: 40px; top: 602px; font-size: 19px; color: #ffffff; }
</style>
</head>
<body>
  <div class="business-card">
    <div class="brand">
      <span class="brand-dot"></span>
      <span class="brand-name">Tormin Group</span>
    </div>

    <h1 class="person-name">Rami Haddad</h1>
    <p class="person-title">Managing Partner</p>
    <p class="direct-line direct-phone">Phone: +971 (0)50 318 7042</p>
    <p class="direct-line direct-email">Email: rami@tormingroup.com</p>

    <div class="divider"></div>

    <div class="office office-head">
      <h2>Head Office</h2>
      <p>P.O. Box: 41208 Abu Dhabi. U.A.E</p>
      <p>Tel No: +971 (0)2 5137290</p>
      <p>Fax No: +971(0)2 5137291</p>
      <p>Email: sales@tormingroup.com</p>
    </div>
    <div class="office office-dubai">
      <h2>Dubai Office</h2>
      <p>P.O. Box: 572164 Dubai, U.A.E</p>
      <p>Tel No: +971 (0)4 386502</p>
      <p>Fax No: +971(0)4 386517</p>
      <p>Email: sales@tormingroup.com</p>
    </div>
    <div class="office office-doha">
      <h2>Qater Office</h2>
      <p>P.O. Box: 27830 Doha, Qatter</p>
      <p>Tel No: +974 44715306</p>
      <p>Fax No: +971 44715309</p>
      <p>Email: sales@tormingroup.com</p>
    </div>

    <svg class="footer-bands" viewBox="0 0 640 40" preserveAspectRatio="none" aria-hidden="true">
      <path d="M414 40 L421 30 Q425 28 431 28 H640 V40 Z" fill="var(--band-light)" stroke="#fff" stroke-width="3"/>
      <path d="M204 40 L216 25 C221 19 227 18 234 18 H394 C404 18 411 22 417 30 L424 40 Z" fill="var(--band-dark)" stroke="#fff" stroke-width="3"/>
      <path d="M0 8 H186 C196 8 202 14 208 20 L220 40 H0 Z" fill="var(--accent-red)"/>
    </svg>
    <p class="web-address">www.tormingroup.com</p>
  </div>
</body>
</html>
```